Business Card Design For Office Furniture Clearance Company

Kestrel Office Clearance - our company name pretty much explains what we do, we clear offices for high end clients, mainly plc's and large international companies.

We require a nice looking business card that displays professionalism but without being too serious.

It would be nice to see just a little more than a conventional boring business card, make sure you add some flare.

Industry/Entity Type

Office Furniture

Contact Information for Business Card

CARD 1

Mark Holloway
Director
mark@kestrelofficeclearance.co.uk
m: 07700 153928

t: 01632 960418
www.kestrelofficeclearance.co.uk

Kestrel Office Clearance
Unit K4 B
2-8 Fenwick Lane
Ashworth
Fernbridge
ZZ9 4QT

tidy office moves… handled from start to finish.

CARD 2

Peter Radford
Director
peter@kestrelofficeclearance.co.uk
m: 07700 382615

t: 01632 960418

Kestrel Office Clearance
Unit K4 B
2-8 Fenwick Lane
Ashworth
Fernbridge
ZZ9 4QT

Font styles to use
Sans Serif

Requirements
Must have
• A white background - as we have a blue logo.
Nice to have
• Nice use of the logo - play around with this and dissect it.

```html
<!DOCTYPE html>
<html lang="en">
<head>
<meta charset="utf-8">
<title>Kestrel Office Clearance – Business Card</title>
<link rel="stylesheet" href="https://fonts.googleapis.com/css2?family=Open+Sans:wght@400;600;700&display=swap">
<style>
  :root {
    --bg: #e9e7e3;
    --brand-blue: #1a7fc4;
    --brand-blue-light: #3a9ad8;
    --brand-blue-dark: #0f64a3;
    --card-white: #ffffff;
    --card-grey: #e4e6e8;
    --tagline-grey: #6b6f73;
    --text-white: #ffffff;
  }
  * { box-sizing: border-box; margin: 0; padding: 0; }
  html, body {
    width: 1200px; height: 843px; overflow: hidden;
    background: var(--bg);
    font-family: "Open Sans", Arial, sans-serif;
  }
  .canvas { position: relative; width: 1200px; height: 843px; }

  .card {
    position: absolute; width: 540px; height: 330px;
    border-radius: 4px; overflow: hidden;
    box-shadow: 0 10px 24px rgba(0,0,0,.18);
  }

  /* Front card */
  .card-front {
    left: 60px; top: 90px;
    background: linear-gradient(180deg, var(--card-white) 55%, var(--card-grey) 100%);
  }
  .front-disc {
    position: absolute; left: -10px; top: 45px;
    width: 240px; height: 240px; border-radius: 50%;
    background: radial-gradient(circle at 40% 35%, var(--brand-blue-light), var(--brand-blue) 60%, var(--brand-blue-dark));
  }
  .front-wordmark {
    position: absolute; left: 252px; top: 128px;
    font-size: 21px; font-weight: 600; color: var(--brand-blue);
    letter-spacing: .2px; white-space: nowrap;
  }
  .front-tagline {
    position: absolute; left: 252px; top: 160px;
    font-size: 13.5px; line-height: 19px; color: var(--tagline-grey);
    white-space: nowrap;
  }

  /* Back card */
  .card-back {
    left: 600px; top: 420px;
    background: linear-gradient(180deg, var(--card-white) 55%, var(--card-grey) 100%);
  }
  .back-panel {
    position: absolute; left: 0; top: 0; width: 395px; height: 100%;
    background: linear-gradient(135deg, var(--brand-blue-light) 0%, var(--brand-blue) 55%, var(--brand-blue-dark) 100%);
  }
  .person-name {
    position: absolute; left: 30px; top: 26px;
    font-size: 19px; font-weight: 600; color: var(--text-white);
    letter-spacing: .6px; text-transform: uppercase;
  }
  .person-role {
    position: absolute; left: 30px; top: 52px;
    font-size: 11px; color: var(--text-white); letter-spacing: .5px;
    text-transform: uppercase;
  }
  .address {
    position: absolute; left: 30px; top: 92px;
    font-size: 13.5px; line-height: 19px; color: var(--text-white); font-style: normal;
  }
  .address .company { font-weight: 700; }
  .contact-list {
    position: absolute; left: 30px; top: 190px; list-style: none;
    font-size: 13.5px; line-height: 22px; color: var(--text-white);
  }
  .contact-list li { display: flex; align-items: center; gap: 8px; white-space: nowrap; }
  .contact-list svg { width: 13px; height: 13px; fill: var(--text-white); flex: none; }

  .back-disc {
    position: absolute; left: 315px; top: 105px;
    width: 160px; height: 160px; border-radius: 50%;
    background: radial-gradient(circle at 40% 35%, var(--brand-blue-light), var(--brand-blue) 60%, var(--brand-blue-dark));
    border: 4px solid var(--card-white);
    box-shadow: 0 0 0 1px rgba(15,100,163,.35);
    display: flex; align-items: center; justify-content: center; text-align: center;
    font-size: 15px; line-height: 19px; font-weight: 600; color: var(--text-white);
  }
</style>
</head>
<body>
<main class="canvas">

  <section class="card card-front" aria-label="Card front">
    <div class="front-disc"></div>
    <p class="front-wordmark">Kestrel Office Clearance</p>
    <p class="front-tagline">tidy office moves…<br>handled from start to finish.</p>
  </section>

  <section class="card card-back" aria-label="Card back">
    <div class="back-panel">
      <p class="person-name">Mark Holloway</p>
      <p class="person-role">Director</p>
      <address class="address">
        <span class="company">Kestrel Office Clearance</span><br>
        Unit K4 B, 2-8 Fenwick Lane<br>
        Ashworth, Fernbridge<br>
        ZZ9 4QT
      </address>
      <ul class="contact-list">
        <li>
          <svg viewBox="0 0 16 16" aria-hidden="true"><path d="M3.6 1.2l2.3 2.6-1.3 2c.9 2 2.6 3.7 4.6 4.6l2-1.3 2.6 2.3-1.5 2.2C7 13.6 2.4 9 1.4 3z"/></svg>
          01632 960418
        </li>
        <li>
          <svg viewBox="0 0 16 16" aria-hidden="true"><path d="M4.5 0.5h7a1 1 0 0 1 1 1v13a1 1 0 0 1-1 1h-7a1 1 0 0 1-1-1v-13a1 1 0 0 1 1-1zm.8 2v9.5h5.4V2.5zM8 12.8a.9.9 0 1 0 0 1.8.9.9 0 0 0 0-1.8z"/></svg>
          07700 153928
        </li>
        <li>
          <svg viewBox="0 0 16 16" aria-hidden="true"><path d="M1 3h14v10H1zm1.5 1.3v.4L8 8.6l5.5-3.9v-.4zm0 2.2v5.2h11V6.5L8 10.4z"/></svg>
          mark@kestrelofficeclearance.co.uk
        </li>
        <li>
          <svg viewBox="0 0 16 16" aria-hidden="true"><path d="M8 1a7 7 0 1 0 0 14A7 7 0 0 0 8 1zm-1 2.3c-.6.9-1.6 1.3-1.6 2.4 0 1 1.3 1 1.8 1.8.4.8-.3 1.8.4 2.6.6.7 0 2.3 0 2.3A5.6 5.6 0 0 1 3.3 4.6zM9.6 3c1.9.6 3.2 2.3 3.3 4.3-.7-.5-1.6-.2-2.1.4-.6.7-1.600.2-1.800-.7-.2-1 .9-1.4.6-2.4-.1-.6-.8-.8 0-1.600z"/></svg>
          www.kestrelofficeclearance.co.uk
        </li>
      </ul>
    </div>
    <div class="back-disc">Kestrel<br>Office<br>Clearance</div>
  </section>

</main>
</body>
</html>
```